Marwick Family Chiropractic Stationary

The letterhead and business card must have our logo.
We would like to see the logo used in different ways ( It can be expanded upon in the stationary.)
Please use the the same or similar colors.
Must be eye catching and memorable.
Must be easy to read

Reason: The doctor has been too busy to make any final decisions. He would like to give himself a little more time.

Target Market(s)

Chiropractic Healthcare

Industry/Entity Type

Business

Requirements
Must have
• Dr. Leonard Marwick D.C.
Chiropractor

860-555-0183

417 Birchfield Road, 2nd Floor
Vernon, CT 06091

drmarwick@marwickspine.example
www.marwickspine.example
www.facebook.com/MarwickFamilySpine
Should not have
• should not be difficult to read

```html
<!DOCTYPE html>
<html lang="en">
<head>
<meta charset="utf-8">
<title>Marwick Family Chiropractic Stationery</title>
<link href="https://fonts.googleapis.com/css2?family=Didact+Gothic&display=swap" rel="stylesheet">
<style>
  :root {
    --ink: #000000;
    --leaf-green: #a6cf5b;
    --trunk-grey: #8f8478;
    --soft-grey: #b9b3ac;
    --paper: #ffffff;
    --backdrop: #e9e6e2;
    --rule: #9a9a9a;
  }
  * { margin: 0; padding: 0; box-sizing: border-box; }
  html, body { width: 1200px; height: 720px; overflow: hidden; }
  body {
    background: var(--backdrop);
    font-family: "Didact Gothic", "Century Gothic", sans-serif;
    position: relative;
  }
  .card {
    position: absolute;
    width: 544px;
    height: 310px;
    overflow: hidden;
  }
  .card--front { left: 42px; top: 36px; background: var(--ink); }
  .card--mark-dark { left: 618px; top: 34px; background: var(--ink); }
  .card--wordmark { left: 42px; top: 372px; background: var(--ink); }
  .card--mark-light { left: 620px; top: 368px; background: var(--leaf-green); }

  /* brand name stand-in */
  .brand {
    position: absolute;
    left: 0; right: 0;
    text-align: center;
    font-family: "Didact Gothic", "Century Gothic", sans-serif;
    letter-spacing: 0.04em;
  }
  .brand__dot {
    display: block;
    margin: 0 auto 10px;
    border-radius: 50%;
  }

  /* front card */
  .front__brand { top: 22px; color: var(--leaf-green); }
  .front__brand .brand__dot { width: 62px; height: 62px; background: var(--leaf-green); }
  .front__brand .brand__name { font-size: 25px; line-height: 1.15; }
  .front__brand .brand__sub { font-size: 12.5px; letter-spacing: 0.06em; }

  .doctor {
    position: absolute;
    right: 270px;
    top: 200px;
    text-align: right;
  }
  .doctor__name { color: var(--leaf-green); font-size: 14.5px; }
  .doctor__title { color: var(--trunk-grey); font-size: 13px; margin-top: 4px; }

  .contact-divider {
    position: absolute;
    left: 283px;
    top: 203px;
    width: 1px;
    height: 52px;
    background: var(--paper);
  }
  .contact-list {
    position: absolute;
    left: 286px;
    top: 178px;
    list-style: none;
    color: var(--paper);
    font-size: 13.5px;
  }
  .contact-list li {
    display: flex;
    align-items: center;
    height: 21.5px;
  }
  .contact-list svg { width: 11px; height: 11px; margin-right: 7px; flex: none; }

  .front__rule {
    position: absolute;
    left: 0; right: 0;
    top: 276px;
    height: 2px;
    background: var(--rule);
  }
  .address-band {
    position: absolute;
    left: 0; right: 0;
    bottom: 0;
    height: 26px;
    background: var(--leaf-green);
    color: var(--ink);
    font-size: 13.5px;
    letter-spacing: 0.08em;
    text-align: center;
    line-height: 26px;
    font-weight: 700;
  }

  /* mark cards */
  .mark__brand { top: 64px; }
  .mark__brand .brand__dot { width: 120px; height: 120px; }
  .mark__brand .brand__name { font-size: 22px; }
  .card--mark-dark .brand { color: var(--leaf-green); }
  .card--mark-dark .brand__dot { background: var(--leaf-green); }
  .card--mark-light .brand { color: var(--paper); }
  .card--mark-light .brand__dot { background: var(--paper); }

  .web {
    position: absolute;
    left: 0; right: 0;
    bottom: 22px;
    text-align: center;
    color: var(--paper);
    font-size: 15px;
    letter-spacing: 0.14em;
  }

  /* wordmark card */
  .pattern-field {
    position: absolute;
    inset: 0;
    background: radial-gradient(circle at 50% 45%, #1d2413 0%, #0c0f08 70%);
  }
  .wordmark {
    position: absolute;
    left: 0; right: 0;
    top: 90px;
    text-align: center;
    color: var(--leaf-green);
  }
  .wordmark__name { font-size: 76px; line-height: 1; letter-spacing: 0.03em; }
  .wordmark__sub { font-size: 28px; letter-spacing: 0.03em; margin-top: 8px; }
</style>
</head>
<body>

<section class="card card--front">
  <div class="brand front__brand">
    <span class="brand__dot"></span>
    <div class="brand__name">MARWICK</div>
    <div class="brand__sub">FAMILY CHIROPRACTIC</div>
  </div>

  <div class="doctor">
    <div class="doctor__name">Dr. Leonard Marwick D.C.</div>
    <div class="doctor__title">Chiropractor</div>
  </div>

  <div class="contact-divider"></div>

  <ul class="contact-list">
    <li>
      <svg viewBox="0 0 12 12" aria-hidden="true"><path d="M3 1 L5 3.5 L4 5 Q5.5 7 7 8 L8.5 7 L11 9 L9.5 11 Q4 10 1 3 Z" fill="#a6cf5b"/></svg>
      860-555-0183
    </li>
    <li>
      <svg viewBox="0 0 12 12" aria-hidden="true"><rect x="1" y="3" width="10" height="7" fill="none" stroke="#a6cf5b" stroke-width="1.3"/><path d="M1 3 L6 7 L11 3" fill="none" stroke="#a6cf5b" stroke-width="1.3"/></svg>
      mymarwick@marwickspine.example
    </li>
    <li>
      <svg viewBox="0 0 12 12" aria-hidden="true"><circle cx="6" cy="6" r="5" fill="none" stroke="#a6cf5b" stroke-width="1.2"/><ellipse cx="6" cy="6" rx="2.2" ry="5" fill="none" stroke="#a6cf5b" stroke-width="1"/><line x1="1" y1="6" x2="11" y2="6" stroke="#a6cf5b" stroke-width="1"/></svg>
      www.marwickspine.example
    </li>
    <li>
      <svg viewBox="0 0 12 12" aria-hidden="true"><rect x="1" y="1" width="10" height="10" fill="#3b5998"/></svg>
      MarwickFamilySpine
    </li>
  </ul>

  <div class="front__rule"></div>
  <div class="address-band">417 Birchfield Road, 2nd Floor, Vernon, CT 06091</div>
</section>

<section class="card card--mark-dark">
  <div class="brand mark__brand">
    <span class="brand__dot"></span>
    <div class="brand__name">Marwick Family Chiropractic</div>
  </div>
  <div class="web">www.marwickspine.example</div>
</section>

<section class="card card--wordmark">
  <div class="pattern-field" role="img" aria-label="Repeating pattern of the practice tree mark in muted green and olive on black"></div>
  <div class="wordmark">
    <div class="wordmark__name">MARWICK</div>
    <div class="wordmark__sub">FAMILY CHIROPRACTIC</div>
  </div>
  <div class="web">www.marwickspine.example</div>
</section>

<section class="card card--mark-light">
  <div class="brand mark__brand">
    <span class="brand__dot"></span>
    <div class="brand__name">Marwick Family Chiropractic</div>
  </div>
  <div class="web">www.marwickspine.example</div>
</section>

</body>
</html>
```